Letter and Envelope Design For Harborline Realty

Please design a letter and an envelope incorporating our logo (See Attached). We are also launched a business card contest. Since we want them to match, please feel free to submit a design for both the business card and also the letter design and envelope.

Requirements
Must have
• The envelope, the letter and the business cards must match somehow connecting the designs. We want them to have something that holds them together besides the logo.

```html
<!DOCTYPE html>
<html lang="en">
<head>
<meta charset="utf-8">
<title>Harborline Realty — Letterhead and Envelopes</title>
<link href="https://fonts.googleapis.com/css2?family=Montserrat:wght@600&family=Questrial&display=swap" rel="stylesheet">
<style>
  :root {
    --navy: #001a8c;
    --grey: #5a5a5a;
    --ink: #4a4a4a;
    --paper: #f7f7f7;
    --stage: #dedede;
    --faint: #e9e9ee;
  }
  * { margin: 0; padding: 0; box-sizing: border-box; }
  html, body { width: 1200px; height: 877px; overflow: hidden; background: var(--stage); }
  body { position: relative; font-family: "Questrial", sans-serif; color: var(--ink); }

  .sheet { position: absolute; background: var(--paper); overflow: hidden; }
  .letter { left: 69px; top: 64px; width: 528px; height: 742px; }
  .envelope-back { left: 614px; top: 269px; width: 531px; height: 241px; }
  .envelope-front { left: 614px; top: 563px; width: 533px; height: 242px; }

  .brand { position: absolute; text-align: center; }
  .brand-mark { display: block; margin: 0 auto 6px; border: 2px solid var(--navy); border-radius: 50%; }
  .brand-name {
    font-family: "Montserrat", sans-serif; font-weight: 600; color: var(--navy);
    letter-spacing: 1.5px; line-height: 1.25; text-transform: uppercase;
  }

  .letter .brand { left: 47px; top: 40px; width: 122px; }
  .letter .brand-mark { width: 46px; height: 46px; }
  .letter .brand-name { font-size: 12px; }

  .contact { position: absolute; top: 148px; font-size: 8px; line-height: 11px; color: var(--ink); }
  .contact-address { left: 202px; }
  .contact-phone { left: 311px; }
  .contact-web { left: 389px; }
  .contact-row { display: flex; align-items: center; gap: 4px; }
  .contact-row svg { width: 7px; height: 7px; fill: var(--navy); }

  .watermark-ring {
    position: absolute; border: 8px solid var(--faint); border-radius: 50%;
  }
  .letter .watermark-ring { left: 125px; top: 214px; width: 318px; height: 318px; }
  .envelope-front .watermark-ring { left: 315px; top: 23px; width: 196px; height: 196px; border-width: 6px; }

  .letter-body { position: absolute; left: 47px; top: 214px; width: 440px; }
  .salutation { font-size: 14px; margin-bottom: 21px; color: var(--ink); }
  .letter-body p { font-size: 7.6px; line-height: 11.4px; margin-bottom: 11.4px; text-align: left; }
  .closing { margin-top: 22px; }
  .signature {
    position: absolute; left: 43px; top: 520px; width: 95px; height: 38px;
    background: linear-gradient(90deg, rgba(0,26,140,.12), rgba(0,26,140,.05));
    border-radius: 4px;
  }

  .wave { position: absolute; left: 0; bottom: 0; width: 100%; }
  .letter .wave { height: 62px; }
  .envelope-front .wave { height: 54px; }

  .flap {
    position: absolute; left: 0; top: 0; width: 100%; height: 74px;
    background: var(--navy);
    clip-path: polygon(0 0, 100% 0, 98.5% 60%, 96% 100%, 4% 100%, 1.5% 60%);
    border-radius: 0 0 22px 22px;
    display: flex; align-items: center; justify-content: center; gap: 8px;
  }
  .flap .brand-mark { margin: 0; width: 30px; height: 30px; border-color: #fff; }
  .flap .brand-name { color: #fff; font-size: 10px; }

  .envelope-front .brand { left: 29px; top: 26px; width: 104px; }
  .envelope-front .brand-mark { width: 38px; height: 38px; }
  .envelope-front .brand-name { font-size: 10px; }
  .return-address { position: absolute; left: 32px; top: 98px; width: 98px; text-align: center; font-size: 8px; line-height: 10px; }
</style>
</head>
<body>

<section class="sheet letter">
  <div class="watermark-ring"></div>

  <div class="brand">
    <span class="brand-mark"></span>
    <div class="brand-name">Harborline<br>Realty</div>
  </div>

  <div class="contact contact-address">4120 Tidewater Road<br>Juneau, Alaska 99801</div>
  <div class="contact contact-phone">
    <div class="contact-row"><svg viewBox="0 0 10 10"><path d="M2 0l2 2-1 1.5c.7 1.5 2 2.8 3.5 3.5L8 6l2 2-1.5 2C4 9.5.5 6 0 1.5z"/></svg>555 210 4471</div>
    <div class="contact-row"><svg viewBox="0 0 10 10"><path d="M2.5 0h5v10h-5zM3.5 1v7h3V1z"/></svg>555 382 9016</div>
  </div>
  <div class="contact contact-web">
    <div class="contact-row"><svg viewBox="0 0 10 10"><path d="M0 2h10v6H0zM0 2l5 3.5L10 2"/></svg>mail@harborline.com</div>
    <div class="contact-row"><svg viewBox="0 0 10 10"><circle cx="5" cy="5" r="5"/></svg>www.harborline.com</div>
  </div>

  <div class="letter-body">
    <div class="salutation">Dear Mr. Carter,</div>
    <p>Lorem ipsum dolor sit amet, consectetur adipiscing elit. Donec orci purus, luctus vitae dignissim eu, iaculis sed purus. Vivamus faucibus, ipsum nec aliquet viverra, leo mauris condimentum ligula, sit amet sagittis enim ligula quis arcu. Nam egestas tortor id nisi porttitor mattis. In tortor ante, ultricies in suscipit a, tempus non massa. Vivamus et auctor mi. Fusce vel massa nulla. Phasellus nec eros mauris, et scelerisque orci.</p>
    <p>Donec malesuada orci vitae nulla accumsan porta a id massa. Quisque accumsan iaculis magna sit amet fringilla. Maecenas consequat, magna eget tincidunt semper, odio nibh rutrum mi, id feugiat ante nisi eu risus. Vestibulum nunc orci, rhoncus a placerat in, ultricies in mi. Cras mattis varius eros, vel fringilla nisi suscipit eget. Quisque scelerisque sagittis nulla at porttitor.</p>
    <p>Sed id augue vitae urna euismod commodo aliquet a quam. Pellentesque arcu velit, cursus et malesuada ut, consequat et diam. Nullam erat sem, rhoncus id ullamcorper vitae, rhoncus et arcu. In ultricies ultricies nulla, ut rutrum nisi iaculis at. Donec eu magna a metus ornare faucibus. Fusce aliquet faucibus ultricies. Morbi semper, est id tincidunt gravida, sem arcu adipiscing lacus, ac bibendum nulla leo eu purus. Quisque nec diam sed risus consectetur a ccumsan quis quis nibh. Vestibulum id purus lorem.</p>
    <p>It is a long established fact that a reader will be distracted by the readable content of a page when looking at its layout. The point of using Lorem Ipsum is that it has a more-or-less normal distribution of letters, as opposed to using 'Content here, content here', making it look like readable English. Many desktop publishing packages</p>
    <p class="closing">Sincerely,</p>
  </div>
  <div class="signature" role="img" aria-label="Handwritten signature of Daniel Carter"></div>

  <svg class="wave" viewBox="0 0 528 62" preserveAspectRatio="none" aria-hidden="true">
    <path d="M0 0 C60 40 160 50 260 42 C360 34 450 16 528 22 L528 30 C440 26 360 42 260 50 C160 58 60 48 0 18Z" fill="var(--grey)"/>
    <path d="M0 22 C70 54 170 60 270 52 C370 44 450 30 528 34 L528 62 L0 62Z" fill="var(--navy)"/>
    <path d="M20 44 C120 64 300 56 528 38" fill="none" stroke="#fff" stroke-width="1"/>
  </svg>
</section>

<section class="sheet envelope-back">
  <div class="flap">
    <span class="brand-mark"></span>
    <span class="brand-name">Harborline Realty</span>
  </div>
</section>

<section class="sheet envelope-front">
  <div class="watermark-ring"></div>

  <div class="brand">
    <span class="brand-mark"></span>
    <div class="brand-name">Harborline<br>Realty</div>
  </div>
  <div class="return-address">4120 Tidewater Road<br>Juneau, Alaska 99801</div>

  <svg class="wave" viewBox="0 0 533 54" preserveAspectRatio="none" aria-hidden="true">
    <path d="M0 0 C60 34 160 44 260 36 C360 28 450 12 533 18 L533 26 C440 22 360 36 260 44 C160 52 60 42 0 16Z" fill="var(--grey)"/>
    <path d="M0 20 C70 48 170 52 270 45 C370 38 450 26 533 30 L533 54 L0 54Z" fill="var(--navy)"/>
    <path d="M20 38 C120 56 300 50 533 34" fill="none" stroke="#fff" stroke-width="1"/>
  </svg>
</section>

</body>
</html>
```